Business Card Design for company

We want new business cards. We'd like something different-- yet still highly professional. Our tagline is Providing leadership, delivering success. Stock photos are ok, as long as they are relevant and look upscale.

Target Market(s)

Architecture/Business Management Consulting/Engineering Consulting

Contact Information for Business Card

dark gray background with pops of blue might be good, but you tell me. You're the designers. Rounded corners might be nice, but again, you tell me.

Font styles to use
Serif
Sans Serif

Colors
3276b5
5c5c5c
9d9d9d
fbfbfb

Requirements
Nice to have
• Something different, but still very professional.

```html
<!DOCTYPE html>
<html lang="en">
<head>
<meta charset="utf-8">
<title>Norvale Partners – Business Card</title>
<link href="https://fonts.googleapis.com/css2?family=Work+Sans:wght@400;500;600&display=swap" rel="stylesheet">
<style>
  :root {
    --blue: #2f6aa3;
    --ink: #3c3f46;
    --grey: #5c5c5c;
    --light: #9d9d9d;
    --paper: #fbfbfb;
    --slate: #3b404a;
    --slate-text: #d9dadc;
    --stage: #e4e5e7;
  }
  * { margin: 0; padding: 0; box-sizing: border-box; }
  html, body { width: 1200px; height: 900px; overflow: hidden; }
  body {
    background: var(--stage);
    font-family: "Work Sans", Arial, sans-serif;
    position: relative;
  }
  .card {
    position: absolute;
    left: 337px;
    width: 525px;
    height: 300px;
    box-shadow: 0 6px 18px rgba(0,0,0,0.18);
  }
  .card--front { top: 110px; background: var(--paper); color: var(--grey); }
  .card--back { top: 480px; background: var(--slate); }

  .holder { position: absolute; left: 28px; top: 26px; }
  .holder__name {
    color: var(--blue); font-size: 18px; font-weight: 500;
    letter-spacing: 1.5px; text-transform: uppercase;
  }
  .holder__role { font-size: 11px; color: var(--grey); margin-top: 2px; }

  .contact { position: absolute; left: 28px; top: 190px; list-style: none; font-size: 12px; }
  .contact li { display: flex; align-items: center; gap: 8px; height: 19px; color: var(--grey); }
  .contact svg { width: 9px; height: 9px; fill: none; stroke: var(--blue); stroke-width: 1.4; }
  .contact .accent { color: var(--blue); }

  .brand { position: absolute; display: flex; align-items: center; gap: 8px; font-weight: 600; text-transform: uppercase; }
  .brand__mark { background: var(--blue); }
  .card--front .brand { right: 30px; top: 118px; color: var(--ink); font-size: 20px; letter-spacing: 2px; }
  .card--front .brand__mark { width: 14px; height: 14px; }

  .address { position: absolute; right: 30px; bottom: 26px; text-align: right; font-size: 12px; line-height: 17px; color: var(--grey); }

  .card--back .brand { left: 0; right: 0; top: 110px; justify-content: center; color: var(--slate-text); font-size: 30px; letter-spacing: 3px; gap: 12px; }
  .card--back .brand__mark { width: 20px; height: 20px; }
  .web-rule {
    position: absolute; left: 60px; right: 60px; top: 200px;
    display: flex; align-items: center; gap: 12px;
    color: var(--slate-text); font-size: 11px; letter-spacing: 1px;
  }
  .web-rule::before, .web-rule::after { content: ""; flex: 1; height: 1px; background: var(--light); }
</style>
</head>
<body>
  <section class="card card--front">
    <div class="holder">
      <p class="holder__name">Daniel Hartley</p>
      <p class="holder__role">Director</p>
    </div>
    <ul class="contact">
      <li><svg viewBox="0 0 10 10"><path d="M2 1 L4 1 L4.5 3 L3.3 4 Q4.5 6.2 6 6.7 L7 5.5 L9 6 L9 8 Q5 9 2 5 Q1 3 2 1 Z"/></svg>(555) 010-4821</li>
      <li><svg viewBox="0 0 10 10"><rect x="1" y="2" width="8" height="6"/><path d="M1 2 L5 5.5 L9 2"/></svg>info@norvalepartners.com</li>
      <li><svg viewBox="0 0 10 10"><circle cx="5" cy="5" r="4"/><path d="M1 5 H9 M5 1 Q2.5 5 5 9 M5 1 Q7.5 5 5 9"/></svg><span>www.<span class="accent">norvalepartners</span>.com</span></li>
    </ul>
    <div class="brand"><span class="brand__mark"></span>Norvale Partners</div>
    <p class="address">218b Harlow Street,<br>Ashford, NZ, 4020</p>
  </section>

  <section class="card card--back">
    <div class="brand"><span class="brand__mark"></span>Norvale Partners</div>
    <p class="web-rule">www.norvalepartners.com</p>
  </section>
</body>
</html>
```